Business Card Design for Marketing Firm

Looking for business card design for higher end marketing firm. Clean but impressionable/trendy. We are a marketing firm that represents manufacturers in the foodservice equipment and supply industry. Our customers are end users such has hotels, restaurants, country clubs, convention centers and casinos as well as distributors of restaurants supplies and equipment, and manufacturers of foodservice equipment and supplies.
Target Market(s)
Hotels, Restaurants, Supply & Equipment Distributors, Foodservice Manufacturers
Industry/Entity Type
Foodservice/Hospitality
Contact Information for Business Card
Name, Title, Contact Number, Email, Website, Social Media, Address
Requirements
Must have
- Clean & Simple but Serious and Impressionable

```html
<!DOCTYPE html>
<html lang="en">
<head>
<meta charset="utf-8">
<title>Meridian Hospitality Reps — Business Card</title>
<link href="https://fonts.googleapis.com/css2?family=Libre+Baskerville:wght@400;700&family=Arimo:wght@400&display=swap" rel="stylesheet">
<style>
  :root {
    --navy: #0a0a7a;
    --navy-text: #14148a;
    --paper: #f7f7f8;
    --ink: #1e1e24;
    --grey: #6b6b73;
    --stage: #e9e9ec;
    --white: #ffffff;
  }
  * { box-sizing: border-box; margin: 0; padding: 0; }
  html, body { width: 1200px; height: 912px; overflow: hidden; background: var(--stage); }
  .canvas { position: relative; width: 1200px; height: 912px; }

  .card {
    position: absolute;
    width: 560px; height: 320px;
    border-radius: 22px;
    overflow: hidden;
  }

  /* Back side */
  .card-back { left: 90px; top: 100px; background: var(--navy); }
  .back-name {
    position: absolute; left: 0; right: 0; top: 112px;
    text-align: center;
    font-family: "Libre Baskerville", serif; font-weight: 400;
    font-size: 46px; letter-spacing: 6px; color: var(--white);
  }
  .back-url {
    position: absolute; left: 0; right: 0; top: 226px;
    text-align: center;
    font-family: "Arimo", sans-serif; font-size: 15px;
    letter-spacing: 3px; color: var(--white);
  }

  /* Front side */
  .card-front { left: 550px; top: 492px; background: var(--paper); }
  .social { position: absolute; left: 34px; top: 30px; display: flex; gap: 6px; }
  .social span { width: 22px; height: 22px; border-radius: 50%; background: var(--navy); display: block; }

  .brand { position: absolute; right: 34px; top: 34px; text-align: right; }
  .brand-name {
    font-family: "Libre Baskerville", serif; font-weight: 400;
    font-size: 20px; letter-spacing: 1px; color: var(--navy-text);
    border-bottom: 1.5px solid var(--navy-text); padding-bottom: 3px;
  }
  .brand-sub {
    font-family: "Libre Baskerville", serif; font-size: 11px;
    letter-spacing: 1.5px; color: var(--navy-text); margin-top: 3px;
  }

  .divider { position: absolute; left: 0; right: 0; top: 150px; height: 1px; background: var(--ink); }
  .address {
    position: absolute; right: 34px; top: 106px; text-align: right;
    font-family: "Arimo", sans-serif; font-size: 13px; line-height: 18px; color: var(--ink);
  }

  .person { position: absolute; left: 34px; top: 176px; }
  .person-name {
    font-family: "Libre Baskerville", serif; font-weight: 700;
    font-size: 24px; letter-spacing: 0.5px; color: var(--navy-text);
  }
  .person-title { font-family: "Arimo", sans-serif; font-size: 14px; color: var(--grey); margin-top: 2px; }
  .person-rule { width: 220px; height: 1px; background: var(--ink); margin: 8px 0 8px; }
  .contact { list-style: none; font-family: "Arimo", sans-serif; font-size: 14px; color: var(--ink); }
  .contact li { display: flex; align-items: center; gap: 8px; line-height: 20px; }
  .contact svg { width: 12px; height: 12px; fill: var(--navy); flex: none; }
</style>
</head>
<body>
<main class="canvas">
  <section class="card card-back" aria-label="Card back">
    <div class="back-name">MERIDIAN</div>
    <div class="back-url">www.MERIDIAN.com</div>
  </section>

  <section class="card card-front" aria-label="Card front">
    <div class="social" aria-label="Social media"><span></span><span></span><span></span></div>

    <div class="brand">
      <div class="brand-name">MERIDIAN HOSPITALITY</div>
      <div class="brand-sub">REPS</div>
    </div>

    <div class="address">4120 Harborview Lane<br>Glen Cove, NY 11542</div>
    <div class="divider"></div>

    <div class="person">
      <div class="person-name">DANIEL MERCER</div>
      <div class="person-title">President</div>
      <div class="person-rule"></div>
      <ul class="contact">
        <li><svg viewBox="0 0 24 24"><path d="M6.6 10.8a15 15 0 0 0 6.6 6.6l2.2-2.2c.3-.3.7-.4 1-.2 1.1.4 2.3.6 3.6.6.6 0 1 .4 1 1V20c0 .6-.4 1-1 1C10.6 21 3 13.4 3 4c0-.6.4-1 1-1h3.5c.6 0 1 .4 1 1 0 1.3.2 2.5.6 3.6.1.3 0 .7-.2 1z"/></svg>(555) 0147-2290</li>
        <li><svg viewBox="0 0 24 24"><path d="M2 5h20v14H2zm2 2v.5l8 5 8-5V7l-8 5z"/></svg>name@MERIDIAN.com</li>
        <li><svg viewBox="0 0 24 24"><circle cx="12" cy="12" r="10"/></svg>www.MERIDIAN.com</li>
      </ul>
    </div>
  </section>
</main>
</body>
</html>
```